Website offering services oriented to the metaverse and blockchain

We need an ecommerce website theme/template for a new company named Vimbral (a play on words for KORVAND the inventor of Quorvex). Vimbral will provide metaverse services such as:
• Vimbral Coin
• Vimbral wallet
• Vimbral Exchange
• Vimbral NFT
• Vimbral Tech
• Vimbral Pay
• Vimbral CaaS (community as a service)
• Vimbral CRM
• Vimbral Experience
• Vimbral Blockchain
• Vimbral Commerce
• Vimbral Space (as in outer space)
• Vimbral Art (sub of NFT)
• Vimbral Store

You can find our actual logo at the following link, in order to show us templates aligned with our brand:
https://files.brindlevault.net/share/folders/8kLmTzqWpXcVbNdRyHsEfGaUoJi2QtYxP?mode=view

Looking forward to heard back from you,

Designs look the same

We need a WordPress ecommerce website theme/template for a new company named Vimbral (a play on words for KORVAND the inventor of Quorvex). Vimbral will provide metaverse services such as: • Vimbral Coin • Vimbral wallet • Vimbral Exchange • Vimbral NFT • Vimbral Tech • Vimbral Pay • Vimbral CaaS (community as a service) • Vimbral CRM • Vimbral Experience • Vimbral Blockchain • Vimbral Commerce • Vimbral Space (as in outer space) • Vimbral Art (sub of NFT) • Vimbral Store You can find our actual logo at the following link, in order to show us templates aligned with our brand: https://files.brindlevault.net/share/folders/8kLmTzqWpXcVbNdRyHsEfGaUoJi2QtYxP?mode=view Looking forward to heard back from you,

Target Market(s)

Blockchain & Cryptocurrency Businesses

Industry/Entity Type

B2C, B2B Services.

Other font styles liked:
• Monserrat, Helvetica, Object Sans

Requirements
Nice to have
• Light background picture,
Should not have
• Arch designs

```html
<!DOCTYPE html>
<html lang="en">
<head>
<meta charset="utf-8">
<title>Vimbral — Cryptocurrency Makes Everything Better</title>
<link href="https://fonts.googleapis.com/css2?family=Poppins:wght@600;700&family=Fira+Sans+Condensed:wght@400;500;600&family=Roboto:wght@400;500&display=swap" rel="stylesheet">
<style>
:root{
  --night:#1d0b58;
  --royal:#3a168f;
  --violet:#4e10d8;
  --hero-a:#2d1a78;
  --hero-b:#5a3fb4;
  --white:#ffffff;
  --ink:#3a1aa8;
  --line:rgba(255,255,255,.85);
}
*{margin:0;padding:0;box-sizing:border-box}
html,body{width:1200px;height:3482px;overflow:hidden}
body{position:relative;background:var(--night);color:var(--white);font-family:"Fira Sans Condensed",sans-serif}
.abs{position:absolute}
.brand{font-family:"Poppins",sans-serif;font-weight:700;font-size:30px;letter-spacing:.5px;color:var(--white)}

/* hero */
.hero{left:0;top:0;width:1200px;height:698px;background:linear-gradient(120deg,var(--hero-a) 0%,#4a2fa0 45%,var(--hero-b) 70%,#3b238c 100%)}
.hero .brand{left:112px;top:50px}
.nav{left:425px;top:62px;display:flex;gap:28px;font-family:"Roboto",sans-serif;font-size:16px}
.btn-login{left:861px;top:52px;width:108px;height:38px;border:1.5px solid var(--white);border-radius:4px;font-family:"Roboto",sans-serif;font-size:16px;display:flex;align-items:center;justify-content:center}
.btn-register{left:981px;top:52px;width:108px;height:38px;background:var(--white);color:var(--ink);border-radius:4px;font-family:"Roboto",sans-serif;font-size:16px;display:flex;align-items:center;justify-content:center}
.hero h1{left:110px;top:192px;font-family:"Poppins",sans-serif;font-weight:700;font-size:62px;line-height:81px;width:640px}
.hero p{left:111px;top:452px;width:480px;font-family:"Roboto",sans-serif;font-size:15px;line-height:33px}
.btn-start{left:112px;top:557px;width:130px;height:47px;background:var(--white);color:var(--ink);border-radius:4px;font-family:"Poppins",sans-serif;font-weight:600;font-size:15px;display:flex;align-items:center;justify-content:center}

/* about */
.about{left:0;top:698px;width:1200px;height:585px;background:var(--night)}
.about-art{left:119px;top:49px;width:458px;height:469px;border:6px solid #e8e6f2;border-radius:6px;background:linear-gradient(135deg,#5312e0,#4a0ccf)}
.about h2{left:646px;top:82px;font-weight:600;font-size:42px}
.about h3{left:646px;top:158px;font-weight:600;font-size:20px}
.about .lead{left:646px;top:190px;width:450px;font-weight:500;font-size:14.5px;line-height:30px}
.about .small{left:645px;top:302px;width:450px;font-family:"Roboto",sans-serif;font-size:11px;line-height:30px}
.btn-read{left:645px;top:423px;width:132px;height:43px;background:var(--white);color:var(--ink);border-radius:4px;font-weight:600;font-size:15px;display:flex;align-items:center;justify-content:center}
.watch{left:832px;top:420px;display:flex;align-items:center;gap:12px}
.watch-text{font-weight:500;font-size:15px;line-height:26px}

/* services */
.services{left:0;top:1283px;width:1200px;height:658px;background:radial-gradient(circle at 80% 20%,#4a23a8 0%,var(--royal) 45%,#33128a 100%)}
.services h2{left:0;width:1200px;text-align:center;top:40px;font-weight:600;font-size:42px}
.services h3{left:0;width:1200px;text-align:center;top:110px;font-weight:600;font-size:42px}
.services h3 u{text-underline-offset:6px;text-decoration-thickness:2px}
.card{top:208px;width:298px;height:363px;border:2px solid var(--line);padding:42px 18px 0}
.card h4{font-weight:600;font-size:25px;margin:20px 0 18px}
.card p{font-weight:500;font-size:14.5px;line-height:26px}
.card .more{margin-top:22px;font-weight:500;font-size:19px}
.arrow{top:377px;width:42px;height:46px;background:var(--white);display:flex;align-items:center;justify-content:center}

/* team */
.team{left:0;top:1941px;width:1200px;height:610px;background:var(--night)}
.team h2{left:0;width:1200px;text-align:center;top:62px;font-weight:600;font-size:42px}
.team h2 u{text-underline-offset:6px;text-decoration-thickness:2px}
.team p{left:0;width:1200px;text-align:center;top:136px;font-weight:500;font-size:15px;line-height:23px}
.member{top:254px;width:221px;height:269px}
.m1{background:linear-gradient(180deg,#5c6478,#2a2c44)}
.m2{background:linear-gradient(180deg,#9aa6a8,#3d4d77)}
.m3{background:linear-gradient(180deg,#9fa4b0,#d8cbb4)}
.m4{background:linear-gradient(180deg,#c8ccd0,#2b2f45)}
.member-info{left:0;top:160px;width:221px;text-align:center}
.member-info .name{font-weight:500;font-size:21px}
.member-info .role{font-weight:500;font-size:14px;margin-top:4px}
.socials{display:flex;justify-content:center;gap:10px;margin-top:10px}
.socials span{width:22px;height:22px;border-radius:4px;background:var(--white)}

/* contact */
.contact{left:0;top:2551px;width:1200px;height:496px;background:linear-gradient(135deg,#3c1a9a,#4b27b0 50%,#3a1894)}
.contact h2{left:0;width:1212px;text-align:center;top:40px;font-family:"Roboto",sans-serif;font-weight:500;font-size:23px;letter-spacing:1px}
.field{top:100px;width:296px;height:60px;border:1.5px solid rgba(255,255,255,.75);font-family:"Roboto",sans-serif;font-size:15px;padding:20px 10px}
.message{left:136px;top:200px;width:923px;height:183px;border:1.5px solid rgba(255,255,255,.75);font-family:"Roboto",sans-serif;font-size:15px;padding:12px 10px}
.btn-contact{left:505px;top:410px;width:172px;height:54px;background:var(--night);font-family:"Roboto",sans-serif;font-size:20px;display:flex;align-items:center;justify-content:center}

/* footer */
.footer{left:0;top:3047px;width:1200px;height:435px;background:var(--night)}
.footer .brand{left:112px;top:50px}
.footer .about-txt{left:112px;top:128px;width:270px;font-family:"Roboto",sans-serif;font-size:14px;line-height:26px}
.footer h5{top:68px;font-weight:500;font-size:20px}
.contact-list{left:413px;top:125px;list-style:none;font-weight:500;font-size:15px}
.contact-list li{display:flex;align-items:center;gap:16px;height:39px}
.links{left:673px;top:125px;list-style:none;font-family:"Roboto",sans-serif;font-size:16px;line-height:30.5px}
.map{left:857px;top:124px;width:231px;height:166px;background:linear-gradient(135deg,#eef0f2,#dfe6e8 60%,#e9edf0)}
.rule{left:112px;top:347px;width:976px;height:1px;background:rgba(255,255,255,.7)}
.copy{left:0;width:1200px;text-align:center;top:372px;font-weight:500;font-size:14px}
</style>
</head>
<body>

<section class="abs hero" role="img" aria-label="Purple city skyline at night overlaid with glowing security icons">
  <div class="abs brand">Vimbral</div>
  <nav class="abs nav"><span>Home</span><span>About</span><span>Our services</span><span>Team</span><span>How its Work</span></nav>
  <div class="abs btn-login">Login</div>
  <div class="abs btn-register">Register</div>
  <h1 class="abs">Cryptocurrency Makes Everything Better.</h1>
  <p class="abs">Lorem ipsum dolor sit amet, consectetur adipiscing elit. Ut elit tellus, luctus nec ullamcorper mattis, pulvinar dapibus leo.</p>
  <div class="abs btn-start">Get Stared</div>
</section>

<section class="abs about">
  <div class="abs about-art" role="img" aria-label="Isometric illustration of a laptop with floating screens and folders"></div>
  <h2 class="abs">About Vimbral</h2>
  <h3 class="abs">Why to choose Vimbral?</h3>
  <p class="abs lead">Lorem ipsum dolor sit amet, consectetur adipiscing elit. Duis at dictum risus, non suscipit arcu. Quisque aliquam posuere tortor, sit amet convallis nunc scelerisque in.</p>
  <p class="abs small">Lorem ipsum dolor sit amet, consectetur adipiscing elit. Aenean cursus tincidunt ultrices. Ut quis blandit dolor. Ut laoreet sagittis arcu eu tristique. Vestibulum ante ipsum primis in faucibus orci luctus et ultrices posuere</p>
  <div class="abs btn-read">Read More</div>
  <div class="abs watch">
    <svg width="52" height="52" viewBox="0 0 52 52"><circle cx="26" cy="26" r="24" fill="none" stroke="#fff" stroke-width="2.5"/><path d="M20 16 L36 26 L20 36 Z" fill="#fff"/></svg>
    <div class="watch-text">WATCH VIDEO<br>What and How it work</div>
  </div>
</section>

<section class="abs services">
  <h2 class="abs">Our Services</h2>
  <h3 class="abs">Best &amp; Secured <u>Crypto Services</u></h3>

  <div class="abs arrow" style="left:51px"><svg width="14" height="18" viewBox="0 0 14 18"><path d="M12 1 L2 9 L12 17 Z" fill="#3a168f"/></svg></div>
  <div class="abs arrow" style="left:1106px"><svg width="14" height="18" viewBox="0 0 14 18"><path d="M2 1 L12 9 L2 17 Z" fill="#3a168f"/></svg></div>

  <div class="abs card" style="left:112px">
    <svg width="60" height="60" viewBox="0 0 60 60"><circle cx="30" cy="30" r="27" fill="none" stroke="#fff" stroke-width="4"/><circle cx="30" cy="30" r="13" fill="#fff"/></svg>
    <h4>Crypto Service</h4>
    <p>Lorem ipsum dolor sit amet, consectetur adipiscing elit. Ut elit tellus, luctus nec ullamcorper mattis, pulvinar dapibus leo.</p>
    <div class="more">Learn More &nbsp; »»</div>
  </div>
  <div class="abs card" style="left:451px">
    <svg width="64" height="60" viewBox="0 0 64 60"><g fill="#fff"><path d="M32 2 L44 8 L32 14 L20 8 Z"/><path d="M20 11 L31 17 V30 L20 24 Z"/><path d="M44 11 L33 17 V30 L44 24 Z"/><path d="M18 28 L30 34 L18 40 L6 34 Z"/><path d="M6 37 L17 43 V56 L6 50 Z"/><path d="M30 37 L19 43 V56 L30 50 Z"/><path d="M46 28 L58 34 L46 40 L34 34 Z"/><path d="M34 37 L45 43 V56 L34 50 Z"/><path d="M58 37 L47 43 V56 L58 50 Z"/></g></svg>
    <h4>Crypto Transaction</h4>
    <p>Lorem ipsum dolor sit amet, consectetur adipiscing elit. Ut elit tellus, luctus nec ullamcorper mattis, pulvinar dapibus leo.</p>
    <div class="more">Learn More &nbsp; »»</div>
  </div>
  <div class="abs card" style="left:789px">
    <svg width="60" height="60" viewBox="0 0 60 60" fill="none" stroke="#fff" stroke-width="2.5"><circle cx="16" cy="10" r="6"/><path d="M6 26 q10-12 20 0"/><rect x="34" y="4" width="22" height="16" rx="2"/><path d="M40 12 l4 4 l7-8"/><rect x="4" y="32" width="52" height="24" rx="4"/><circle cx="30" cy="44" r="7"/><circle cx="12" cy="44" r="2"/><circle cx="48" cy="44" r="2"/></svg>
    <h4>Crypto Investment</h4>
    <p>Lorem ipsum dolor sit amet, consectetur adipiscing elit. Ut elit tellus, luctus nec ullamcorper mattis, pulvinar dapibus leo.</p>
    <div class="more">Learn More &nbsp; »»</div>
  </div>
</section>

<section class="abs team">
  <h2 class="abs">Our Professionals <u>Team</u></h2>
  <p class="abs">Lorem ipsum dolor sit amet, consectetur adipiscing elit. Ut elit tellus,<br>luctus nec ullamcorper mattis, pulvinar dapibus leo.</p>
  <div class="abs member m1" style="left:120px" role="img" aria-label="Portrait photo of a smiling team member in a suit">
    <div class="abs member-info">
      <div class="name">Delia Marchetti</div>
      <div class="role">Blockchain Analyst</div>
      <div class="socials"><span></span><span></span><span></span></div>
    </div>
  </div>
  <div class="abs member m2" style="left:369px" role="img" aria-label="Portrait photo of a team member in a blue suit"></div>
  <div class="abs member m3" style="left:617px" role="img" aria-label="Portrait photo of a team member in a beige jacket"></div>
  <div class="abs member m4" style="left:865px" role="img" aria-label="Portrait photo of a team member in a dark suit"></div>
</section>

<section class="abs contact">
  <h2 class="abs">GET IN TOUCH</h2>
  <div class="abs field" style="left:138px">Full name</div>
  <div class="abs field" style="left:451px">Phone Number</div>
  <div class="abs field" style="left:765px">Email Id</div>
  <div class="abs message">Massages</div>
  <div class="abs btn-contact">CONTACT US</div>
</section>

<footer class="abs footer">
  <div class="abs brand">Vimbral</div>
  <p class="abs about-txt">Lorem ipsum dolor sit amet, consectetur adipiscing elit. Nullam in nibh vehicula.</p>

  <h5 class="abs" style="left:413px">Get In Touch</h5>
  <ul class="abs contact-list">
    <li><svg width="14" height="16" viewBox="0 0 14 16"><path d="M7 1a5 5 0 0 1 5 5c0 4-5 9-5 9s-5-5-5-9a5 5 0 0 1 5-5z" fill="#fff"/><circle cx="7" cy="6" r="2" fill="#1d0b58"/></svg>27 Larkspur Lane, Westbrook</li>
    <li><svg width="14" height="12" viewBox="0 0 14 12" fill="none" stroke="#fff" stroke-width="1.6"><rect x="1" y="1" width="12" height="10"/><path d="M1 1 L7 7 L13 1"/></svg>hello@vimbral.io</li>
    <li><svg width="14" height="14" viewBox="0 0 14 14"><path d="M3 1 L5.5 1 L6.5 4.5 L5 5.5 Q6 8 8.5 9 L9.5 7.5 L13 8.5 L13 11 Q12 13 10 13 Q1 11 1 3 Q1 1 3 1Z" fill="#fff"/></svg>+1 555 010 2233</li>
    <li><svg width="14" height="14" viewBox="0 0 14 14" fill="none" stroke="#fff" stroke-width="1.6"><circle cx="7" cy="7" r="6"/><path d="M7 3.5 V7 H10"/></svg>09.00 AM - 17.00 PM</li>
  </ul>

  <h5 class="abs" style="left:673px;top:64px">Quicklinks</h5>
  <ul class="abs links"><li>Home</li><li>About</li><li>Our services</li><li>Team</li><li>How its Work</li></ul>

  <h5 class="abs" style="left:857px">Location</h5>
  <div class="abs map" role="img" aria-label="Street map showing the office location"></div>

  <div class="abs rule"></div>
  <div class="abs copy">Copyright © 2021 &nbsp;Vimbral.</div>
</footer>

</body>
</html>
```